Business Card Design Project

Business card based on attached logo

Todd Merrick
Todd@lorvantest.com
877-514-9073 ext. 318
Www.LorvanTest.com

Industry/Entity Type

Business

```html
<!DOCTYPE html>
<html lang="en">
<head>
<meta charset="utf-8">
<title>LorvanTest Business Cards</title>
<link rel="stylesheet" href="https://fonts.googleapis.com/css2?family=Source+Sans+3:wght@400;600;700&family=Questrial&display=swap">
<style>
  :root {
    --stage: #c7a27c;
    --label: #2a1c12;
    --card-white: #ffffff;
    --card-grey-top: #f2f2f2;
    --card-grey-bottom: #e4e4e4;
    --brand-red: #e0232c;
    --red-top: #d7232a;
    --red-bottom: #a01b21;
    --ink: #111111;
    --text-grey: #3a3a3a;
    --panel-line: #d2d2d2;
  }
  * { box-sizing: border-box; margin: 0; padding: 0; }
  html, body { width: 1200px; height: 788px; overflow: hidden; }
  body {
    position: relative;
    background: var(--stage);
    font-family: "Source Sans 3", Arial, sans-serif;
  }
  .view-label {
    position: absolute;
    width: 525px;
    text-align: center;
    font-family: "Source Sans 3", Arial, sans-serif;
    font-size: 21px;
    color: var(--label);
  }
  .card {
    position: absolute;
    width: 525px;
    height: 300px;
    border-radius: 22px;
    overflow: hidden;
    background: var(--card-white);
  }
  .card--red { background: linear-gradient(180deg, var(--red-top), var(--red-bottom)); }
  .card--grey { background: linear-gradient(180deg, var(--card-grey-top), var(--card-grey-bottom)); }

  .brand {
    position: absolute;
    display: flex;
    align-items: flex-start;
    gap: 8px;
  }
  .brand__name {
    font-family: "Source Sans 3", Arial, sans-serif;
    font-weight: 700;
    color: var(--ink);
    line-height: 1;
    letter-spacing: -0.5px;
  }
  .brand__mark { background: var(--brand-red); flex: none; }
  .brand--centered { left: 0; right: 0; justify-content: center; }

  .web {
    position: absolute;
    left: 0; right: 0;
    text-align: center;
    font-family: "Questrial", Arial, sans-serif;
    font-size: 19px;
    color: var(--text-grey);
  }
  .card--red .web { color: var(--card-white); }

  /* Front */
  .front__accent {
    position: absolute; left: 0; top: 173px;
    width: 8px; height: 36px; background: var(--brand-red);
  }
  .front__person {
    position: absolute; left: 28px; top: 180px;
    font-weight: 700; font-size: 18px; color: var(--brand-red);
  }
  .contact {
    position: absolute; left: 28px;
    display: flex; align-items: center; gap: 5px;
    font-family: "Questrial", Arial, sans-serif;
    font-size: 14px; color: var(--text-grey);
  }
  .contact svg { width: 11px; height: 11px; fill: var(--brand-red); }
  .contact--web { left: auto; right: 29px; }
  .dot { width: 8px; height: 8px; border-radius: 50%; background: var(--brand-red); }

  /* Back 3 panel */
  .plate {
    position: absolute; left: 81px; top: 82px;
    width: 360px; height: 128px;
    background: var(--card-white);
    border: 1px solid var(--panel-line);
  }
</style>
</head>
<body>

  <div class="view-label" style="left:54px; top:33px;">Front</div>
  <div class="view-label" style="left:622px; top:33px;">Back - 1</div>
  <div class="view-label" style="left:54px; top:403px;">Back - 2</div>
  <div class="view-label" style="left:622px; top:403px;">Back - 3</div>

  <!-- Front -->
  <section class="card card--front" style="left:54px; top:74px;">
    <div class="brand" style="left:28px; top:52px;">
      <span class="brand__name" style="font-size:54px;">LorvanTest</span>
      <span class="brand__mark" style="width:14px; height:14px;"></span>
    </div>
    <div class="front__accent"></div>
    <div class="front__person">Todd Merrick</div>
    <div class="contact" style="top:246px;">
      <svg viewBox="0 0 24 24" aria-hidden="true"><path d="M6.6 10.8a15.1 15.1 0 0 0 6.6 6.6l2.2-2.2a1 1 0 0 1 1-.25 11.4 11.4 0 0 0 3.6.57 1 1 0 0 1 1 1V20a1 1 0 0 1-1 1A17 17 0 0 1 3 4a1 1 0 0 1 1-1h3.5a1 1 0 0 1 1 1c0 1.25.2 2.45.57 3.57a1 1 0 0 1-.25 1z"/></svg>
      <span>877-514-9073 ext. 318</span>
    </div>
    <div class="contact" style="top:268px;">
      <svg viewBox="0 0 24 24" aria-hidden="true"><path d="M2 5h20v14H2zm2 2v.5l8 5 8-5V7zm0 3v7h16v-7l-8 5z"/></svg>
      <span>Todd@lorvantest.com</span>
    </div>
    <div class="contact contact--web" style="top:268px;">
      <span class="dot"></span>
      <span>www.LorvanTest.com</span>
    </div>
  </section>

  <!-- Back 1 -->
  <section class="card card--back" style="left:622px; top:74px;">
    <div class="brand brand--centered" style="top:84px;">
      <span class="brand__name" style="font-size:62px;">LorvanTest</span>
      <span class="brand__mark" style="width:16px; height:16px;"></span>
    </div>
    <div class="web" style="top:247px;">www.LorvanTest.com</div>
  </section>

  <!-- Back 2 -->
  <section class="card card--red" style="left:54px; top:445px;">
    <div class="brand brand--centered" style="top:84px;">
      <span class="brand__name" style="font-size:62px;">LorvanTest</span>
      <span class="brand__mark" style="width:16px; height:16px; background:var(--card-white);"></span>
    </div>
    <div class="web" style="top:252px;">www.LorvanTest.com</div>
  </section>

  <!-- Back 3 -->
  <section class="card card--grey" style="left:622px; top:445px;">
    <div class="plate">
      <div class="brand brand--centered" style="top:40px;">
        <span class="brand__name" style="font-size:44px;">LorvanTest</span>
        <span class="brand__mark" style="width:12px; height:12px;"></span>
      </div>
    </div>
    <div class="web" style="top:252px;">www.LorvanTest.com</div>
  </section>

</body>
</html>
```